business card deign

Logo needs the following on it.
1. attached logo
2. Tagline - "From chilled drinks to a lively crowd...we bring it all!"
3. Name- Dalton Pikes, Founder and CPO
4. Address - 412 E. Carver Avenue, Ste 2207, Tampa, FL. 33917
5. Phone - 555.318.4726

```html
<!DOCTYPE html>
<html lang="en">
<head>
<meta charset="utf-8">
<title>Boundry – Business Card</title>
<link href="https://fonts.googleapis.com/css2?family=Arimo:wght@400;700&display=swap" rel="stylesheet">
<style>
  :root {
    --backdrop: #3a3a3a;
    --card: #2d2d2d;
    --ink: #ffffff;
    --ink-soft: #e6e6e6;
  }
  * { margin: 0; padding: 0; box-sizing: border-box; }
  html, body {
    width: 1200px;
    height: 803px;
    overflow: hidden;
    background: var(--backdrop);
    font-family: "Arimo", Arial, sans-serif;
    color: var(--ink);
  }
  .stage {
    position: relative;
    width: 1200px;
    height: 803px;
  }
  .card {
    position: absolute;
    top: 247px;
    width: 540px;
    height: 309px;
    background: var(--card);
    border-radius: 22px;
    box-shadow: 0 14px 30px rgba(0,0,0,0.35);
    overflow: hidden;
  }
  .card--contact { left: 40px; }
  .card--brand { left: 620px; }

  /* contact side */
  .brand-word {
    position: absolute;
    left: 42px;
    top: 58px;
    font-size: 24px;
    font-weight: 700;
    letter-spacing: 0.55em;
  }
  .person {
    position: absolute;
    left: 42px;
    top: 106px;
  }
  .person__name {
    font-size: 19px;
    font-weight: 700;
    letter-spacing: -0.01em;
  }
  .person__role {
    font-size: 13px;
    color: var(--ink-soft);
    margin-top: 2px;
  }
  .address {
    position: absolute;
    left: 42px;
    top: 162px;
    font-size: 13px;
    line-height: 1.35;
    color: var(--ink-soft);
    font-style: normal;
  }
  .contacts {
    position: absolute;
    left: 42px;
    top: 226px;
    list-style: none;
    font-size: 13px;
    line-height: 1.4;
    color: var(--ink-soft);
  }
  .contacts li {
    display: flex;
    align-items: center;
    gap: 8px;
  }
  .contacts svg { width: 11px; height: 11px; fill: var(--ink); }

  /* brand side */
  .lockup {
    position: absolute;
    left: 0;
    right: 0;
    top: 80px;
    text-align: center;
  }
  .lockup__dot {
    display: block;
    width: 62px;
    height: 62px;
    border-radius: 50%;
    background: var(--ink);
    margin: 0 auto 18px;
  }
  .lockup__name {
    font-size: 38px;
    font-weight: 700;
    letter-spacing: 0.45em;
    padding-left: 0.45em;
  }
  .tagline {
    position: absolute;
    left: 0;
    right: 0;
    bottom: 42px;
    text-align: center;
    font-size: 14px;
    color: var(--ink);
  }
</style>
</head>
<body>
<main class="stage">
  <section class="card card--contact">
    <div class="brand-word">BOUNDRY</div>
    <div class="person">
      <div class="person__name">DALTON PIKES</div>
      <div class="person__role">Founder and CPO</div>
    </div>
    <address class="address">
      412 E. Carver Avenue<br>
      Ste 2207<br>
      Tampa, FL. 33917
    </address>
    <ul class="contacts">
      <li>
        <svg viewBox="0 0 24 24" aria-hidden="true"><path d="M6.6 10.8a15.1 15.1 0 0 0 6.6 6.6l2.2-2.2a1 1 0 0 1 1-.25 11.4 11.4 0 0 0 3.6.57 1 1 0 0 1 1 1V20a1 1 0 0 1-1 1A17 17 0 0 1 3 4a1 1 0 0 1 1-1h3.5a1 1 0 0 1 1 1c0 1.25.2 2.45.57 3.57a1 1 0 0 1-.25 1z"/></svg>
        555.318.4726
      </li>
      <li>
        <svg viewBox="0 0 24 24" aria-hidden="true"><path d="M2 5h20v14H2zM4 7v.5l8 5 8-5V7l-8 5z"/></svg>
        info@boundry.com
      </li>
      <li>
        <svg viewBox="0 0 24 24" aria-hidden="true"><path d="M12 2a10 10 0 1 0 0 20 10 10 0 0 0 0-20zm0 2c1 1.3 1.8 3.3 2 6h-4c.2-2.7 1-4.7 2-6zm-2 8h4c-.2 2.7-1 4.7-2 6-1-1.3-1.8-3.3-2-6zM4.1 10h3.9c.1-2 .6-3.8 1.3-5.2A8 8 0 0 0 4.1 10zm0 2a8 8 0 0 0 5.2 7.2c-.7-1.4-1.2-3.2-1.3-5.2zm11.9 0c-.1 2-.6 3.8-1.3 5.2a8 8 0 0 0 5.2-5.2zm3.9-2a8 8 0 0 0-5.2-5.2c.7 1.4 1.2 3.2 1.3 5.2z"/></svg>
        www.boundry.com
      </li>
    </ul>
  </section>

  <section class="card card--brand">
    <div class="lockup">
      <span class="lockup__dot" aria-hidden="true"></span>
      <div class="lockup__name">BOUNDRY</div>
    </div>
    <p class="tagline">From chilled drinks to a lively crowd...we bring it all!</p>
  </section>
</main>
</body>
</html>
```